DRALVO 2020

I have a front picture for the CD; I have all of the info for the back cover; I need someone to put my idea together with the correct specs; I require a very FAST TURN AROUND!!! I need to get this project to the CD replicator by next week ASAP...

```html
<!DOCTYPE html>
<html lang="en">
<head>
<meta charset="utf-8">
<title>DRALVO 2020 – CD Cover</title>
<link rel="stylesheet" href="https://fonts.googleapis.com/css2?family=Inter:wght@800&display=swap">
<style>
  :root {
    --backdrop: #e3e5e7;
    --flag-blue: #2a3a8c;
    --flag-red: #c8202b;
    --flag-white: #e9e6df;
    --stone-grey: #8f8c88;
    --suit-navy: #1b2340;
    --tie-red: #c41f2a;
    --title-white: #f2f3f4;
  }
  * { margin: 0; padding: 0; box-sizing: border-box; }
  html, body {
    width: 1200px;
    height: 907px;
    overflow: hidden;
    background: var(--backdrop);
  }
  .canvas {
    position: relative;
    width: 1200px;
    height: 907px;
  }
  .cover {
    position: absolute;
    left: 190px;
    top: 43px;
    width: 820px;
    height: 820px;
    overflow: hidden;
    box-shadow: 0 6px 24px rgba(0,0,0,0.12);
  }
  .cover__flag-photo {
    position: absolute;
    inset: 0;
    background:
      linear-gradient(160deg,
        var(--flag-blue) 0%,
        var(--flag-blue) 24%,
        var(--flag-red) 40%,
        var(--flag-white) 55%,
        var(--flag-red) 68%,
        var(--flag-white) 78%,
        var(--stone-grey) 100%);
  }
  .cover__portrait-photo {
    position: absolute;
    left: 230px;
    top: 250px;
    width: 460px;
    height: 570px;
    border-radius: 40% 40% 0 0;
    background: linear-gradient(180deg, var(--suit-navy) 0%, #26305a 60%, var(--tie-red) 100%);
    opacity: 0.92;
  }
  .cover__title {
    position: absolute;
    font-family: "Inter", "Helvetica Neue", Arial, sans-serif;
    font-weight: 800;
    color: var(--title-white);
    letter-spacing: -0.05em;
    line-height: 0.8;
    text-shadow: 0 4px 10px rgba(0,0,0,0.25);
  }
  .cover__title--name {
    left: 24px;
    top: 70px;
    font-size: 172px;
  }
  .cover__title--year {
    right: 10px;
    bottom: 40px;
    font-size: 215px;
  }
</style>
</head>
<body>
  <main class="canvas">
    <section class="cover">
      <div class="cover__flag-photo" role="img" aria-label="Photograph of a waving stars-and-stripes flag beside a grey stone wall"></div>
      <div class="cover__portrait-photo" role="img" aria-label="Photograph of a man in a dark suit and red tie with arms spread wide"></div>
      <h1 class="cover__title cover__title--name">DRALVO</h1>
      <p class="cover__title cover__title--year">2020</p>
    </section>
  </main>
</body>
</html>
```